Real Estate Wordpress Landing Page

I'm looking to a landing page dedicated to my real estate brokerage that's catered to promoting that my company provides 1.5% listings to home sellers... I have a couple examples that I'm really looking towards mocking in a version with similar color schemes using my current company colors/website.

http://harbelo.com/
https://www.quarvantis.com/about/one-percent-listing-fee

My brokerage company website is http://www.brightmarrow.us/

Target Market(s)

real estate home sellers & buyers

Industry/Entity Type

Real Estate

Coding

Coded - Design and coding required

Number of Pages Required

1 page

Colors
3176b5
0255a3
eaf1f7
cedeed

Requirements
Must have
• Company website colors - http://www.brightmarrow.us/
• Something around the lines of this website page - http://harbelo.com/
• Wordpress compatibility

```html
<!DOCTYPE html>
<html lang="en">
<head>
<meta charset="utf-8">
<title>Bright Marrow Realty – List for 1.5% Commission</title>
<link href="https://fonts.googleapis.com/css2?family=Montserrat:wght@400;500;600;700&family=Open+Sans:wght@400;600;700&display=swap" rel="stylesheet">
<style>
:root{
  --blue:#0255a3;
  --blue-mid:#3176b5;
  --blue-bright:#0d63b8;
  --ice:#eaf1f7;
  --mist:#cedeed;
  --ink:#2a2a2a;
  --grey:#666;
  --soft:#f2f3f5;
  --footer:#2b2b2b;
  --white:#fff;
}
*{box-sizing:border-box;margin:0;padding:0}
html,body{width:1200px;height:3586px;overflow:hidden}
body{font-family:"Open Sans",Arial,sans-serif;color:var(--ink);background:var(--white);position:relative}
.h{font-family:"Montserrat",Arial,sans-serif}
.abs{position:absolute}

/* header */
.topbar{position:absolute;top:0;left:0;width:1200px;height:5px;background:var(--blue)}
.header{position:absolute;top:5px;left:0;width:1200px;height:131px}
.brand{position:absolute;left:85px;top:28px;display:flex;align-items:center;gap:12px}
.brand-mark{width:34px;height:34px;background:var(--blue)}
.brand-name{font-family:"Montserrat",sans-serif;font-weight:700;font-size:25px;color:var(--blue)}
.contact-item{position:absolute;top:45px;display:flex;align-items:center;gap:18px;font-size:12px;line-height:22px;color:#444}
.contact-ico{width:46px;height:46px;border:1px solid #ccc;border-radius:50%;display:flex;align-items:center;justify-content:center}
.nav{position:absolute;top:136px;left:0;width:1200px;height:54px;background:linear-gradient(#0a5cab,#034e99);display:flex;justify-content:center;align-items:center;gap:38px;border-bottom:3px solid #3d7fc2}
.nav a{color:#fff;text-decoration:none;font-family:"Montserrat",sans-serif;font-size:12px;font-weight:600;letter-spacing:.3px}

/* hero */
.hero{position:absolute;top:190px;left:0;width:1200px;height:535px;background:linear-gradient(180deg,#1b2a44 0%,#2d3d58 45%,#3a3a36 80%,#22211c 100%)}
.hero-title{position:absolute;top:140px;width:100%;text-align:center;color:#fff;font-weight:700;font-size:37px}
.hero-sub{position:absolute;top:193px;width:100%;text-align:center;color:#fff;font-size:26px;font-weight:500}
.search{position:absolute;top:280px;left:348px;width:504px;display:grid;grid-template-columns:248px 248px;gap:8px}
.select{height:40px;background:rgba(20,30,50,.55);border:1px solid rgba(255,255,255,.6);color:#fff;font-size:12px;display:flex;align-items:center;justify-content:space-between;padding:0 12px}
.search-btn{position:absolute;top:438px;left:500px;width:200px;height:42px;background:var(--blue-bright);color:#fff;font-family:"Montserrat",sans-serif;font-weight:600;font-size:15px;display:flex;align-items:center;justify-content:center}

/* welcome */
.welcome-title{position:absolute;left:87px;top:818px;color:var(--blue);font-size:23px;font-weight:600}
.welcome-text{position:absolute;left:87px;top:866px;width:385px;font-size:11px;line-height:27px;color:#555}
.call-line{position:absolute;left:87px;top:1063px;font-size:17px;font-weight:500;color:#222}
.call-phone{position:absolute;left:87px;top:1090px;font-size:37px;font-weight:600;color:var(--blue)}
.ph{position:absolute}

/* projects */
.projects{position:absolute;top:1238px;left:0;width:1200px;height:1140px;background:var(--soft)}
.sec-title{position:absolute;width:100%;text-align:center;color:var(--blue);font-weight:600}
.sec-sub{position:absolute;width:100%;text-align:center;font-size:11px;color:#555}
.card{position:absolute;left:135px;width:930px;background:#fff;border:1px solid #ddd}
.card .img{position:absolute;left:10px;top:10px;width:312px;height:212px}
.card .addr{position:absolute;left:10px;width:312px;text-align:center;font-family:"Montserrat",sans-serif;font-size:14px;font-weight:500;line-height:22px;color:#222}
.card .title{position:absolute;left:360px;top:32px;font-size:18px;font-weight:600;color:var(--blue)}
.card .para{position:absolute;left:362px;top:68px;width:510px;font-size:11.5px;line-height:25px;color:#666}
.card ul{position:absolute;left:362px;top:132px;list-style:none;font-size:12px;color:#444}
.card li{height:32px;display:flex;align-items:center;gap:14px}
.card .rule{position:absolute;left:352px;right:17px;height:1px;background:#ddd}
.card .callus{position:absolute;left:352px;font-family:"Montserrat",sans-serif;font-size:14px;font-weight:600;color:var(--blue)}
.card .mls{position:absolute;right:17px;width:154px;height:38px;background:var(--blue);color:#fff;font-size:11px;display:flex;align-items:center;justify-content:center}

/* testimonial */
.testimonial{position:absolute;top:2378px;left:0;width:1200px;height:316px;background:linear-gradient(90deg,#0b4fa0,#1560b0 50%,#0b4fa0)}
.quote{position:absolute;left:175px;top:100px;width:545px;color:#fff;font-size:12px;line-height:24px}
.qmark{position:absolute;color:#fff;font-size:34px;font-family:Georgia,serif}
.author{position:absolute;left:175px;top:215px;color:#fff;font-weight:700;font-size:14px;font-family:"Montserrat",sans-serif}
.date{position:absolute;left:175px;top:238px;color:#fff;font-size:12px}

/* communities */
.comm{position:absolute;top:2826px;width:247px;height:250px;border:1px solid #ddd;background:#fff}
.comm .img{width:100%;height:190px}
.comm .lbl{height:58px;display:flex;align-items:center;justify-content:center;font-family:"Montserrat",sans-serif;font-size:13px;font-weight:500;color:#333}

/* partners */
.partners{position:absolute;top:3136px;left:0;width:1200px;height:199px;background:#f4f4f4}
.badge{position:absolute;top:49px;width:175px;height:100px;background:#fff;border:1px solid #e3e3e3;display:flex;align-items:center;justify-content:center}
.badge span{width:110px;height:26px;background:var(--mist)}

/* footer */
.footer{position:absolute;top:3335px;left:0;width:1200px;height:251px;background:var(--footer);color:#fff}
.f-head{position:absolute;top:32px;font-family:"Montserrat",sans-serif;font-weight:600;font-size:16px}
.f-text{position:absolute;top:68px;font-size:12px;line-height:29px}
.f-row{display:flex;gap:16px;align-items:center}
.email{position:absolute;left:818px;top:105px;width:295px;height:44px;background:#fff;display:flex;align-items:center;padding-left:18px;color:#888;font-size:12px}
.email b{position:absolute;right:0;top:0;width:46px;height:44px;background:var(--blue);display:flex;align-items:center;justify-content:center}
.copy{position:absolute;top:200px;width:100%;text-align:center;font-size:12px}
.arrow{position:absolute}
</style>
</head>
<body>

<div class="topbar"></div>
<header class="header">
  <div class="brand"><div class="brand-mark"></div><div class="brand-name">Bright Marrow</div></div>
  <div class="contact-item" style="left:515px">
    <div class="contact-ico"><svg width="16" height="16" viewBox="0 0 24 24"><path d="M6.6 10.8a15 15 0 006.6 6.6l2.2-2.2a1 1 0 011-.25 11.4 11.4 0 003.6.6 1 1 0 011 1V20a1 1 0 01-1 1A17 17 0 013 4a1 1 0 011-1h3.5a1 1 0 011 1 11.4 11.4 0 00.6 3.6 1 1 0 01-.25 1z" fill="#555"/></svg></div>
    <div>561-555-0142<br>hello@brightmarrow.us</div>
  </div>
  <div class="contact-item" style="left:722px">
    <div class="contact-ico"><svg width="14" height="18" viewBox="0 0 24 30"><path d="M12 0a10 10 0 00-10 10c0 8 10 20 10 20s10-12 10-20A10 10 0 0012 0zm0 14a4 4 0 110-8 4 4 0 010 8z" fill="#555"/></svg></div>
    <div>820 Lindell Way, Ste 310<br>Boynton Beach, FL 33426</div>
  </div>
  <div class="contact-item" style="left:950px">
    <div class="contact-ico"><svg width="16" height="16" viewBox="0 0 24 24"><circle cx="12" cy="12" r="10" fill="none" stroke="#555" stroke-width="2"/><path d="M12 6v6l4 2" stroke="#555" stroke-width="2" fill="none"/></svg></div>
    <div>9 am to 5 pm<br>Monday thru Friday</div>
  </div>
</header>
<nav class="nav">
  <a href="#">HOME</a><a href="#">FEATURED CITIES</a><a href="#">PROPERTY SEARCH</a><a href="#">EMAIL ALERTS</a><a href="#">COMMUNITIES</a><a href="#">BUYERS &amp; SELLERS</a><a href="#">RENTALS</a><a href="#">INVESTING</a><a href="#">CONTACT</a>
</nav>

<section class="hero" role="img" aria-label="Large suburban house at dusk with lit windows">
  <div class="hero-title h">LIST FOR 1.5% COMMISSION,</div>
  <div class="hero-sub h">&amp; RECEIVE TOP MARKETING FROM REAL ESTATE PRO!</div>
  <div class="search">
    <div class="select">Location :<span>▾</span></div>
    <div class="select">Max. Price<span>▾</span></div>
    <div class="select">Property Type<span>⇕</span></div>
    <div class="select">Beds<span>⇕</span></div>
    <div class="select">Min. Price<span>▾</span></div>
    <div class="select">Baths<span>⇕</span></div>
  </div>
  <div class="search-btn">SEARCH</div>
</section>

<section>
  <h2 class="welcome-title h">WELCOME TO BRIGHT MARROW</h2>
  <p class="welcome-text">We know how frustrating it can be to list your home a bit too low and not receiving the full potential proceeds on the sale of your home and we've also been on the other side of the spectrum where a property is marketed at too high of a price that we don't obtain much traffic to a listing. To avoid these type of issues, we invest in an appraisal report by our licensed appraisers for each of our listings on behalf of our clients!</p>
  <div class="call-line h">CALL US TODAY AND SAVE THOUSANDS $$$</div>
  <div class="call-phone h">561-555-0187</div>
  <div class="ph" style="left:553px;top:768px;width:388px;height:338px;background:linear-gradient(180deg,#1c3d6b,#3b4a5c 60%,#3d6b2e)" role="img" aria-label="Modern two-storey house lit at twilight"></div>
  <div class="ph" style="left:838px;top:860px;width:275px;height:321px;background:linear-gradient(180deg,#e6e6e6,#8a8f96);border:3px solid #fff" role="img" aria-label="Portrait of the listing agent in a suit"></div>
</section>

<section class="projects">
  <h2 class="sec-title h" style="top:36px;font-size:26px">OUR PROJECTS</h2>
  <p class="sec-sub" style="top:84px">To avoid these type of issues, we invest in an appraisal report by our licensed appraisers for each of our listings on behalf of our clients!</p>

  <div class="card" style="top:138px;height:310px">
    <div class="img" style="background:linear-gradient(180deg,#9ec0dc,#d9d2c4 55%,#6f8f52)" role="img" aria-label="Two-storey house with double garage"></div>
    <div class="addr" style="top:238px">214 PALMETTO RIDGE LANE ATLANTIS.</div>
    <div class="title h">SELL WITH BRIGHT MARROW &amp; SAVE $$$</div>
    <p class="para">Sed ut perspiciatis unde omnis iste natus error sit voluptatem accusantium doloremque architecto beatae vitae dicta sunt explicabo.</p>
    <ul><li><svg width="12" height="10"><path d="M1 5l3.5 3.5L11 1" stroke="#0255a3" stroke-width="2" fill="none"/></svg>Professional Real Estate Photography</li><li><svg width="12" height="10"><path d="M1 5l3.5 3.5L11 1" stroke="#0255a3" stroke-width="2" fill="none"/></svg>Complimentary Comparative Market Analysis (CMA)</li><li><svg width="12" height="10"><path d="M1 5l3.5 3.5L11 1" stroke="#0255a3" stroke-width="2" fill="none"/></svg>FREE Consultation with Real Estate Professional</li></ul>
    <div class="rule" style="top:228px"></div>
    <div class="callus" style="top:248px">CALL US : 561-555-0187</div>
    <div class="mls" style="top:240px">BM2071-$550.000</div>
  </div>

  <div class="card" style="top:474px;height:300px">
    <div class="img" style="background:linear-gradient(180deg,#f0efec,#b9b6b0 60%,#6d6a66)" role="img" aria-label="Bright living room interior with sofa"></div>
    <div class="addr" style="top:226px">37 SEAGROVE COURT<br>DEERFIELD BEACH.</div>
    <div class="title h">START YOUR HOME SEARCH WITH US</div>
    <p class="para">Sed ut perspiciatis unde omnis iste natus error sit voluptatem accusantium doloremque architecto beatae vitae dicta sunt explicabo.</p>
    <ul><li><svg width="12" height="10"><path d="M1 5l3.5 3.5L11 1" stroke="#0255a3" stroke-width="2" fill="none"/></svg>Professional Real Estate Photography</li><li><svg width="12" height="10"><path d="M1 5l3.5 3.5L11 1" stroke="#0255a3" stroke-width="2" fill="none"/></svg>Complimentary Comparative Market Analysis (CMA)</li><li><svg width="12" height="10"><path d="M1 5l3.5 3.5L11 1" stroke="#0255a3" stroke-width="2" fill="none"/></svg>FREE Consultation with Real Estate Professional</li></ul>
    <div class="rule" style="top:228px"></div>
    <div class="callus" style="top:248px">CALL US : 561-555-0187</div>
    <div class="mls" style="top:240px">BM2058-$229.500</div>
  </div>

  <div class="card" style="top:797px;height:300px">
    <div class="img" style="background:linear-gradient(180deg,#8fb7dc,#d8c9a8 55%,#5f8a44)" role="img" aria-label="Mediterranean-style house with palm trees"></div>
    <div class="addr" style="top:238px">214 PALMETTO RIDGE LANE ATLANTIS.</div>
    <div class="title h">LEASING &amp; PROPERTY MANAGEMENT</div>
    <p class="para">Sed ut perspiciatis unde omnis iste natus error sit voluptatem accusantium doloremque architecto beatae vitae dicta sunt explicabo.</p>
    <ul><li><svg width="12" height="10"><path d="M1 5l3.5 3.5L11 1" stroke="#0255a3" stroke-width="2" fill="none"/></svg>Professional Real Estate Photography</li><li><svg width="12" height="10"><path d="M1 5l3.5 3.5L11 1" stroke="#0255a3" stroke-width="2" fill="none"/></svg>Complimentary Comparative Market Analysis (CMA)</li><li><svg width="12" height="10"><path d="M1 5l3.5 3.5L11 1" stroke="#0255a3" stroke-width="2" fill="none"/></svg>FREE Consultation with Real Estate Professional</li></ul>
    <div class="rule" style="top:228px"></div>
    <div class="callus" style="top:248px">CALL US : 561-555-0187</div>
    <div class="mls" style="top:240px">BM2071-$550.000</div>
  </div>
</section>

<section class="testimonial">
  <svg class="arrow" style="left:45px;top:120px" width="22" height="80"><path d="M20 2L3 40l17 38" stroke="rgba(255,255,255,.5)" stroke-width="2" fill="none"/></svg>
  <svg class="arrow" style="right:45px;top:120px" width="22" height="80"><path d="M2 2l17 38L2 78" stroke="rgba(255,255,255,.5)" stroke-width="2" fill="none"/></svg>
  <div class="qmark" style="left:155px;top:70px">“</div>
  <p class="quote">Sed ut perspiciatis unde omnis iste natus error sit voluptatem accusantium doloremque laudantium, totam rem aperiam, eaque ipsa quae ab illo inventore veritatis et quasi architecto beatae vitae dicta sunt explicabo. Nemo enim ipsam voluptatem quia voluptas sit aspernatur aut odit aut fugit, sed quia consequuntur magni dolores eos qui ratione voluptatem sequi nesciunt.</p>
  <div class="qmark" style="left:558px;top:175px">”</div>
  <div class="author">DANA WHITLOW</div>
  <div class="date">Posted On 07 July 2018</div>
  <div class="ph" style="left:775px;top:68px;width:196px;height:196px;border-radius:50%;border:4px solid #fff;background:linear-gradient(180deg,#d9cdbf,#8a6b55)" role="img" aria-label="Portrait of a smiling client"></div>
</section>

<section>
  <h2 class="sec-title h" style="top:2722px;font-size:15px">BOYNTON BEACH REALTOR - DISCOVER SOME OF THE BEST COMMUNITIES IN PALM BEACH COUNTY, FL</h2>
  <p class="sec-sub" style="top:2760px">Over here at Bright Marrow Realty, we have some of the best Realtors in the community who are ready to assist you and provide</p>

  <div class="comm" style="left:87px"><div class="img" style="background:linear-gradient(180deg,#8fb9e0,#c9b99a 60%,#6d8a50)" role="img" aria-label="Boca Raton home with palms"></div><div class="lbl">BOCA RATON HOMES FOR SALE</div></div>
  <div class="comm" style="left:347px;background:#0d57a6;border-color:#0d57a6;color:#fff;text-align:center" role="img" aria-label="Jupiter home with blue overlay">
    <div class="h" style="margin-top:58px;font-size:12px;font-weight:600">JUPITER HOMES FOR SALE</div>
    <p style="font-size:11px;line-height:22px;margin:14px 22px 0">Over here at Bright Marrow Realty, we have some of the best Realtors in the community who are ready</p>
    <svg style="margin-top:10px" width="40" height="40"><circle cx="20" cy="20" r="18" fill="none" stroke="#fff" stroke-width="2"/><path d="M20 11v18M11 20h18" stroke="#fff" stroke-width="3"/></svg>
  </div>
  <div class="comm" style="left:607px"><div class="img" style="background:linear-gradient(180deg,#9cc3e6,#d8cbb0 55%,#5f8f3e)" role="img" aria-label="Boynton Beach house with lawn"></div><div class="lbl">BOYNTON BEACH HOMES FOR SALE</div></div>
  <div class="comm" style="left:867px"><div class="img" style="background:linear-gradient(180deg,#a8cdec,#e3d6bd 55%,#7f9a5e)" role="img" aria-label="Lantana two-storey home"></div><div class="lbl">LANTANA HOMES FOR SALE</div></div>
</section>

<section class="partners">
  <svg class="arrow" style="left:45px;top:64px" width="18" height="70"><path d="M16 2L3 35l13 33" stroke="#ccc" stroke-width="2" fill="none"/></svg>
  <svg class="arrow" style="right:45px;top:64px" width="18" height="70"><path d="M2 2l13 33L2 68" stroke="#ccc" stroke-width="2" fill="none"/></svg>
  <div class="badge" style="left:105px"><span></span></div>
  <div class="badge" style="left:310px"><span></span></div>
  <div class="badge" style="left:515px"><span></span></div>
  <div class="badge" style="left:719px"><span></span></div>
  <div class="badge" style="left:922px"><span></span></div>
</section>

<footer class="footer">
  <div class="f-head" style="left:102px">ABOUT BRIGHT MARROW REALTY</div>
  <p class="f-text" style="left:102px;width:300px">Bright Marrow Realty is a Boynton Beach real estate company that prides in our superior service when it Palm Beach County and Broward County areas.</p>
  <div class="f-head" style="left:438px">CONTACT US</div>
  <div class="f-text" style="left:440px">
    <div class="f-row"><svg width="12" height="12"><path d="M11 1L1 5l4 2 2 4z" fill="#fff"/></svg>820 Lindell Way, Ste 310, Boynton Beach, FL 33426</div>
    <div class="f-row"><svg width="12" height="12" viewBox="0 0 24 24"><path d="M6.6 10.8a15 15 0 006.6 6.6l2.2-2.2a1 1 0 011-.25 11.4 11.4 0 003.6.6 1 1 0 011 1V20a1 1 0 01-1 1A17 17 0 013 4a1 1 0 011-1h3.5a1 1 0 011 1 11.4 11.4 0 00.6 3.6 1 1 0 01-.25 1z" fill="#fff"/></svg>561-555-0142, 561-555-0119</div>
    <div class="f-row"><svg width="12" height="10"><rect x=".5" y=".5" width="11" height="9" fill="none" stroke="#fff"/><path d="M.5 .5L6 5l5.5-4.5" stroke="#fff" fill="none"/></svg>hello@brightmarrow.us</div>
  </div>
  <div class="f-head" style="left:818px">NEWSLETTER</div>
  <p class="f-text" style="left:818px">Sed ut perspiciatis unde omnis iste natus error sit</p>
  <div class="email">Enter Your Email Id<b><svg width="18" height="18"><path d="M17 1L1 8l6 2 2 7z" fill="#fff"/></svg></b></div>
  <div class="copy">© Copy Right -2018 Bright Marrow . All rights reserved.</div>
</footer>

</body>
</html>
```